Moridel SA

Découpe de métaux - Fourniture de tôles - Accessoires de machines de chantier (European Patent)

Les designs se ressemblent

Besoin de plus de jours pour examiner

• Mon projet doit comprendre la photo de la halle (bâtiment)

```html
<!DOCTYPE html>
<html lang="fr">
<head>
<meta charset="utf-8">
<title>Moridel SA – Découpe de métaux</title>
<link rel="stylesheet" href="https://fonts.googleapis.com/css2?family=Open+Sans:ital,wdth,wght@1,75,800&family=Roboto+Condensed:ital,wght@0,400;1,400&display=swap">
<style>
  :root {
    --page-bg: #e4e4e6;
    --ink-black: #101012;
    --band-dark: #1d1d21;
    --band-mid: #2c2c31;
    --panel-light: #3d3d44;
    --brand-red: #e0282b;
    --paper-white: #ffffff;
    --headline-light: #f2f2f2;
    --headline-shade: #b9b9bd;
    --photo-deep: #6f6a80;
    --photo-light: #cfcbdc;
    --accent-blue: #3f7fd0;
  }
  html, body {
    margin: 0;
    width: 1200px;
    height: 1200px;
    overflow: hidden;
    background: var(--page-bg);
  }
  .flyer {
    position: absolute;
    left: 80px;
    top: 227px;
    width: 1040px;
    height: 746px;
    display: block;
  }
  .headline {
    font-family: "Open Sans", sans-serif;
    font-style: italic;
    font-weight: 800;
    font-stretch: 75%;
    font-size: 79px;
  }
  .brand-name {
    font-family: "Roboto Condensed", sans-serif;
    font-weight: 400;
    font-size: 34px;
    fill: var(--paper-white);
  }
  .service-list {
    font-family: "Roboto Condensed", sans-serif;
    font-weight: 400;
    font-size: 36px;
    fill: var(--paper-white);
  }
  .service-bullet { fill: var(--brand-red); }
  .patent-note {
    font-family: "Roboto Condensed", sans-serif;
    font-style: italic;
    font-size: 28px;
    fill: var(--paper-white);
  }
  .web-address {
    font-family: "Roboto Condensed", sans-serif;
    font-size: 34px;
    fill: var(--paper-white);
  }
</style>
</head>
<body>
<svg class="flyer" viewBox="0 0 953 684" xmlns="http://www.w3.org/2000/svg" role="group" aria-label="Moridel SA – Découpe de métaux">
  <defs>
    <linearGradient id="top-band-fill" x1="0" y1="0" x2="0" y2="1">
      <stop offset="0" stop-color="var(--band-mid)"/>
      <stop offset="1" stop-color="var(--band-dark)"/>
    </linearGradient>
    <linearGradient id="headline-fill" x1="0" y1="0" x2="0" y2="1">
      <stop offset="0.2" stop-color="var(--headline-light)"/>
      <stop offset="1" stop-color="var(--headline-shade)"/>
    </linearGradient>
    <linearGradient id="photo-fill" x1="0" y1="0" x2="1" y2="1">
      <stop offset="0" stop-color="var(--photo-deep)"/>
      <stop offset="0.55" stop-color="var(--photo-light)"/>
      <stop offset="1" stop-color="var(--photo-deep)"/>
    </linearGradient>
    <linearGradient id="panel-fill" x1="0" y1="0" x2="0" y2="1">
      <stop offset="0" stop-color="var(--panel-light)"/>
      <stop offset="1" stop-color="var(--band-dark)"/>
    </linearGradient>
    <linearGradient id="blue-accent-fill" x1="0" y1="0" x2="1" y2="1">
      <stop offset="0" stop-color="var(--accent-blue)"/>
      <stop offset="1" stop-color="var(--accent-blue)" stop-opacity="0"/>
    </linearGradient>
  </defs>

  <!-- base -->
  <rect class="flyer-base" width="953" height="684" fill="var(--ink-black)"/>

  <!-- title band -->
  <rect class="title-band" width="953" height="114" fill="url(#top-band-fill)"/>
  <rect class="title-rule" x="0" y="52" width="105" height="4" fill="var(--brand-red)"/>
  <text class="headline" x="118" y="84" fill="url(#headline-fill)" textLength="667" lengthAdjust="spacingAndGlyphs">DÉCOUPE DE MÉTAUX</text>
  <rect class="title-underline" x="0" y="114" width="830" height="4" fill="var(--paper-white)"/>

  <!-- photo area -->
  <polygon class="machine-photo" role="img" aria-label="Photo d'une machine CNC de découpe plasma travaillant une tôle métallique"
           points="0,118 821,118 464,622 0,622" fill="url(#photo-fill)"/>

  <!-- diagonal stripes -->
  <polygon class="stripe-red" points="905,0 937,0 452,684 420,684" fill="var(--brand-red)"/>
  <polygon class="stripe-white" points="937,0 967,0 482,684 452,684" fill="var(--paper-white)"/>

  <!-- brand panel -->
  <polygon class="brand-panel" points="770,139 953,139 953,314 625,314" fill="url(#panel-fill)"/>
  <polygon class="brand-panel-accent" points="625,314 712,314 668,398" fill="url(#blue-accent-fill)"/>
  <circle class="brand-dot" cx="745" cy="226" r="18" fill="var(--accent-blue)"/>
  <text class="brand-name" x="775" y="238">Moridel SA</text>

  <!-- services -->
  <text class="service-list" text-anchor="end">
    <tspan x="935" y="457"><tspan class="service-bullet">•</tspan> FOURNITURE</tspan>
    <tspan x="935" y="502">DE TÔLES</tspan>
    <tspan x="925" y="547"><tspan class="service-bullet">•</tspan> Accessoires de</tspan>
    <tspan x="925" y="592">machines de chantier</tspan>
  </text>
  <rect class="services-rule" x="585" y="620" width="368" height="3" fill="var(--brand-red)"/>
  <text class="patent-note" x="928" y="664" text-anchor="end">(EUROPEAN PATENT)</text>

  <!-- web band -->
  <rect class="web-band-white" x="0" y="622" width="75" height="62" fill="var(--paper-white)"/>
  <polygon class="web-band-red" points="75,622 466,622 422,684 75,684" fill="var(--brand-red)"/>
  <g class="globe-icon" fill="none" stroke="var(--brand-red)" stroke-width="2.2">
    <circle cx="42" cy="654" r="16" fill="var(--brand-red)" stroke="none"/>
    <circle cx="42" cy="654" r="10" stroke="var(--paper-white)"/>
    <ellipse cx="42" cy="654" rx="4.5" ry="10" stroke="var(--paper-white)"/>
    <line x1="32" y1="654" x2="52" y2="654" stroke="var(--paper-white)"/>
  </g>
  <text class="web-address" x="117" y="668">MORIDEL.CH</text>
</svg>
</body>
</html>
```